V.Lumo Gin - Bottle label Design

We are manufacturers of Gin in South Africa.
The name of our Gin is V.Lumo Gin with Q standing for Dlovikazi, a Xhosa Village in the region of Eastern Cape.

We would like our brand to depict the following (really the focus of Gold on it)
> Prosperity of the place
> Wealth of the place, land, material or in the people
> Gold rush, potential, hope

As the brand matures, we would like to have campaigns with it. See ideas below:
> V.Lumo Premium
> Crimson dusk edition
Limited edition will be released every year
- V.Lumo entabeni (location)
- V.Lumo ekhayeni (location)

> Each batch of bottles with focus on a specific area/location in Dlovikazi. One that is known and will be highlighted on the map design of the bottle.
Bottles based on landmarks in Dlovikazi and landmark design in the Big V.

Below we tried but we are not where we really want to be in terms of Gin Bottle elegance.

Target Market(s)

Target market is the young crowd. Young Xhosa men and women working really hard to get their goals. Positive thinkers. Elegant. Fresh. Bold. Age from 24 to 45. People who enjoy quality products.

Industry/Entity Type

Beverage Industry. Craft Gin.

Font styles to use
Sans Serif
Decorative

Colors
FFF300
FFF600
FEFA6F
FFFEC7
FFFEE8
FFC000
F8CF3A
FAE287
FDF2CF
FEFAEE

Requirements
Must have
• Gold colour as a theme. Try and make the background textured.

```html
<!DOCTYPE html>
<html lang="en">
<head>
<meta charset="utf-8">
<title>V.Lumo Gin – Bottle Label</title>
<link href="https://fonts.googleapis.com/css2?family=Josefin+Sans:wght@100;300&family=Oswald:wght@400;500&display=swap" rel="stylesheet">
<style>
  :root {
    --backdrop: #e0dace;
    --label: #ffffff;
    --ink: #111111;
    --gold-deep: #7a4f0c;
    --gold-mid: #b8862a;
    --gold-light: #e6e46a;
    --gold-pale: #fffec7;
    --map-tint: #f4f4f5;
    --rule: #222222;
  }
  * { box-sizing: border-box; margin: 0; padding: 0; }
  html, body { width: 1200px; height: 1200px; overflow: hidden; }
  body { background: var(--backdrop); position: relative; font-family: "Oswald", sans-serif; }

  .label {
    position: absolute; left: 96px; top: 197px;
    width: 1007px; height: 805px;
    background: var(--label);
  }

  .pattern-band {
    position: absolute; left: 46px; width: 917px; height: 37px;
    background: linear-gradient(90deg, var(--gold-deep), var(--gold-mid) 20%, var(--gold-light) 40%, var(--gold-mid) 65%, var(--gold-deep));
  }
  .pattern-band.top { top: 20px; }
  .pattern-band.bottom { top: 747px; }

  .village-scene {
    position: absolute; left: 46px; top: 95px; width: 917px; height: 358px;
    background: linear-gradient(180deg, var(--gold-pale) 0%, #d9b56a 30%, #9a6a2a 48%, #e9dfb8 70%, #f6f1dc 100%);
  }

  .brand-mark {
    position: absolute; left: 177px; top: 322px; width: 205px; height: 205px;
    border-radius: 50%;
    background: linear-gradient(90deg, var(--gold-deep), var(--gold-light) 40%, var(--gold-mid) 70%, var(--gold-deep));
    border: 6px solid var(--label);
  }
  .brand-name {
    position: absolute; left: 400px; top: 378px;
    font-family: "Josefin Sans", sans-serif; font-weight: 300;
    font-size: 140px; line-height: 1; color: var(--ink);
    letter-spacing: 2px;
  }

  .village-map {
    position: absolute; left: 47px; top: 499px; width: 235px; height: 233px;
    background: var(--map-tint);
  }

  .info-table {
    position: absolute; left: 47px; top: 587px; width: 914px; height: 146px;
    border: 2px dotted var(--rule);
  }
  .info-table .cell { position: absolute; display: flex; align-items: center; justify-content: center; color: var(--ink); }
  .cell.product {
    left: 0; top: 0; width: 307px; height: 100%;
    border-right: 2px dotted var(--rule);
    font-family: "Josefin Sans", sans-serif; font-weight: 100;
    font-size: 124px; line-height: 1; padding-top: 22px; letter-spacing: 4px;
  }
  .cell.tagline {
    left: 307px; top: 0; right: 0; height: 74px;
    border-bottom: 2px dotted var(--rule);
    font-size: 27px; letter-spacing: 1.6px;
  }
  .cell.strength, .cell.volume { top: 74px; bottom: 0; font-size: 27px; font-weight: 500; }
  .cell.strength { left: 307px; width: 298px; border-right: 2px dotted var(--rule); }
  .cell.volume { left: 605px; right: 0; }
</style>
</head>
<body>
  <main class="label">
    <div class="pattern-band top" role="img" aria-label="Gold geometric diamond and chevron border pattern"></div>

    <div class="village-scene" role="img" aria-label="Gold-toned illustration of Dlovikazi village with hillside, houses and fenced field"></div>

    <div class="brand-mark"></div>
    <div class="brand-name">V.Lumo</div>

    <div class="village-map" role="img" aria-label="Faint street map of Dlovikazi"></div>

    <section class="info-table">
      <div class="cell product">GIN</div>
      <div class="cell tagline">Our Golden Gift from Dlovikazi to the World</div>
      <div class="cell strength">43% alc.vol.</div>
      <div class="cell volume">750 ml</div>
    </section>

    <div class="pattern-band bottom" role="img" aria-label="Gold geometric diamond and chevron border pattern"></div>
  </main>
</body>
</html>
```